Kestrada LLC, needs a web page no more than 5 pages (for now)

Kestrada is a general contractor. Our services include general contracting, design-build construction, disaster recovery and environmental remediation. Our main clients are PMX, TQ, State and Local Gov't Agencies, Hospitals and Schools. Kestrada is also a SDVOSB.

```html
<!DOCTYPE html>
<html lang="en">
<head>
<meta charset="utf-8">
<title>Kestrada LLC — General Contractor</title>
<link rel="stylesheet" href="https://fonts.googleapis.com/css2?family=Outfit:wght@400;500;600&family=Jost:wght@400;500&display=swap">
<style>
:root{
  --black:#000;
  --ink:#0b0b0b;
  --panel:#151515;
  --card:#121212;
  --gold:#e2aa52;
  --gold-deep:#b9843a;
  --gold-soft:#f0c57a;
  --white:#fff;
  --muted:#cfcfcf;
  --line:#8a8a8a;
}
*{box-sizing:border-box;margin:0;padding:0}
html,body{width:1200px;height:3692px;overflow:hidden}
body{position:relative;background:var(--black);color:var(--white);font-family:"Outfit",sans-serif}
.abs{position:absolute}
.gold{color:var(--gold)}
.backdrop{position:absolute;left:0;top:0;width:1200px;height:3692px}

/* header */
.site-header{position:absolute;left:0;top:0;width:1200px;height:90px;background:var(--black)}
.brand-disc{position:absolute;left:128px;top:-40px;width:166px;height:166px;border-radius:50%;background:var(--black)}
.brand{position:absolute;left:148px;top:48px;font-size:24px;font-weight:500;letter-spacing:1px;color:var(--white)}
.nav a{position:absolute;top:32px;font-size:16px;font-weight:500;color:var(--white);text-decoration:none}
.nav a.active{color:var(--gold)}
.nav a.active::before{content:"";position:absolute;left:-2px;right:-2px;top:-32px;height:3px;background:var(--gold)}
.quote-btn{position:absolute;left:919px;top:23px;width:138px;height:41px;border:2px solid var(--gold);border-radius:22px;font-size:15px;font-weight:500;display:flex;align-items:center;justify-content:center}

/* hero */
.hero-title{left:142px;top:278px;font-size:42px;font-weight:500;line-height:49px}
.hero-sub{left:140px;top:388px;font-size:18px;line-height:26px}
.btn{position:absolute;height:40px;border:2px solid var(--gold);border-radius:22px;background:var(--black);font-size:15px;font-weight:500;display:flex;align-items:center;justify-content:center;gap:8px;color:var(--white)}
.arrow-btn{position:absolute;top:665px;width:50px;height:50px;border-radius:50%;border:2px solid var(--gold);background:var(--black);display:flex;align-items:center;justify-content:center}

/* about */
.section-title{position:absolute;font-size:42px;font-weight:500}
.rule{position:absolute;height:2px;background:var(--gold)}
.about-lead{left:631px;top:1000px;width:440px;font-size:21px;font-weight:500;line-height:28px}
.about-text{left:631px;top:1146px;width:425px;font-family:"Jost",sans-serif;font-size:16.5px;line-height:24px;text-align:justify;color:var(--muted)}

/* services */
.service-card{position:absolute;top:1772px;width:211px;height:301px;background:linear-gradient(#1d1d1d,var(--card) 40%);text-align:center}
.service-icon{position:absolute;left:57px;top:-43px;width:98px;height:98px;border-radius:50%;background:var(--gold);box-shadow:0 0 0 18px rgba(226,170,82,.08),0 0 0 36px rgba(226,170,82,.04);display:flex;align-items:center;justify-content:center}
.service-card h3{position:absolute;left:0;right:0;top:120px;font-size:21px;font-weight:500;line-height:29px}
.service-card p{position:absolute;left:18px;right:18px;top:180px;font-family:"Jost",sans-serif;font-size:16px;line-height:24px;color:var(--muted)}

/* clients */
.client{position:absolute;top:2270px;width:170px;height:96px;background:var(--white);color:#111;display:flex;align-items:center;justify-content:center;text-align:center;font-size:20px;line-height:24px}
.client.small{font-size:17px}

/* contact */
.field{position:absolute;border:2px solid #4a4a4a;border-radius:8px;font-family:"Jost",sans-serif;font-size:14px;color:#ccc;padding-left:24px}

/* footer */
.foot-head{position:absolute;font-size:20px;font-weight:600;line-height:28px;letter-spacing:.3px}
.foot-label{position:absolute;font-size:15px;font-weight:600;font-family:"Jost",sans-serif}
.foot-small{position:absolute;font-size:12px;font-family:"Jost",sans-serif;color:#ddd}
.foot-link{position:absolute;font-size:16px;font-family:"Jost",sans-serif;display:flex;gap:14px;align-items:center}
.foot-link::before{content:"»";color:var(--gold);font-size:18px}
.social{position:absolute;top:3498px;width:28px;height:28px;border-radius:50%;background:#2a2a2a}
</style>
</head>
<body>

<svg class="backdrop" viewBox="0 0 1200 3692" aria-hidden="false">
  <defs>
    <linearGradient id="heroFill" x1="0" y1="0" x2="1" y2="1">
      <stop offset="0" stop-color="#5a5651"/>
      <stop offset=".55" stop-color="#3c3935"/>
      <stop offset="1" stop-color="#6d655b"/>
    </linearGradient>
    <linearGradient id="goldBand" x1="0" y1="0" x2="1" y2="0">
      <stop offset="0" stop-color="#a77634"/>
      <stop offset=".6" stop-color="#d9a24f"/>
      <stop offset="1" stop-color="#f2c478"/>
    </linearGradient>
    <linearGradient id="goldSection" x1="0" y1="0" x2="1" y2="1">
      <stop offset="0" stop-color="#e6b262"/>
      <stop offset=".5" stop-color="#cf9b4c"/>
      <stop offset="1" stop-color="#b98a44"/>
    </linearGradient>
  </defs>
  <rect x="0" y="90" width="1200" height="780" fill="url(#heroFill)" role="img" aria-label="Photo of a high-rise under construction with tower cranes against a hazy city skyline"/>
  <polygon points="0,631 600,857 1200,631 1200,1470 0,1470" fill="#000"/>
  <polygon points="455,806 600,846 1200,638 1200,742 600,860" fill="url(#goldBand)"/>
  <rect x="0" y="1460" width="1200" height="505" fill="#161616" role="img" aria-label="Dark textured backdrop of vertical panels"/>
  <polygon points="0,1962 1200,1962 1200,2409 600,2567 0,2409" fill="url(#goldSection)" role="img" aria-label="Gold-toned photo of building scaffolding"/>
  <rect x="0" y="2409" width="1200" height="800" fill="#0e0e0e" role="img" aria-label="Dark grid backdrop"/>
  <polygon points="0,2409 600,2567 1200,2409 1200,2420 600,2578 0,2420" fill="#0e0e0e"/>
  <polygon points="0,2409 600,2567 1200,2409 1200,1962 0,1962" fill="url(#goldSection)"/>
  <polygon points="0,3362 600,3150 746,3205 1200,3205 1200,3692 0,3692" fill="#111"/>
  <polygon points="0,3328 600,3140 746,3205 600,3158 0,3364" fill="url(#goldBand)"/>
</svg>

<header class="site-header">
  <div class="brand-disc"></div>
  <div class="brand">KESTRADA</div>
  <nav class="nav">
    <a class="active" style="left:387px">Home</a>
    <a style="left:474px">About</a>
    <a style="left:561px">Services</a>
    <a style="left:668px">Blog</a>
    <a style="left:745px">Contact</a>
  </nav>
  <svg class="abs" style="left:856px;top:37px" width="15" height="15" viewBox="0 0 15 15"><circle cx="6" cy="6" r="4.5" fill="none" stroke="#fff" stroke-width="2"/><line x1="9.5" y1="9.5" x2="13.5" y2="13.5" stroke="#fff" stroke-width="2.2"/></svg>
  <div class="quote-btn">Get A Quote</div>
</header>

<section class="hero">
  <h1 class="abs hero-title">Building with Integrity.<br><span class="gold">Restoring with Purpose.</span></h1>
  <p class="abs hero-sub">Trusted General Contractor &amp; SDVOSB serving<br>Federal, State, and Local Agencies.</p>
  <div class="btn" style="left:140px;top:462px;width:181px">Request a Proposal</div>
  <div class="btn" style="left:333px;top:462px;width:109px">Contact</div>
  <div class="arrow-btn" style="left:547px"><svg width="12" height="14" viewBox="0 0 12 14"><path d="M8 2 3 7l5 5" fill="none" stroke="#fff" stroke-width="2.4"/></svg></div>
  <div class="arrow-btn" style="left:602px"><svg width="12" height="14" viewBox="0 0 12 14"><path d="M4 2l5 5-5 5" fill="none" stroke="#fff" stroke-width="2.4"/></svg></div>
</section>

<section class="about">
  <svg class="abs" style="left:150px;top:908px" width="442" height="442" viewBox="0 0 442 442">
    <circle cx="221" cy="221" r="216" fill="none" stroke="#e2aa52" stroke-width="2"/>
    <circle cx="129" cy="22" r="8" fill="#e2aa52"/>
    <circle cx="340" cy="403" r="8" fill="#e2aa52"/>
    <circle cx="221" cy="221" r="182" fill="#6b6660" role="img" aria-label="Photo of contractors in hard hats shaking hands over site plans"/>
  </svg>
  <h2 class="section-title" style="left:632px;top:913px">About <span class="gold">Kestrada</span></h2>
  <div class="rule" style="left:632px;top:981px;width:85px"></div>
  <p class="abs about-lead">Kestrada is a <span class="gold">Service-Disabled Veteran-Owned Small Business (SDVOSB)</span> dedicated to delivering reliable, mission-focused construction solutions for federal, state, and local partners.</p>
  <p class="abs about-text">Lorem ipsum dolor sit amet, consectetur adipiscing elit, sed do eiusmod tempor incididunt ut labore et dolore magna aliqua. Ut enim ad minim veniam, quis nostrud exercitation ullamco laboris nisi ut aliquip ex ea commodo consequat. Duis aute irure dolor in reprehenderit in voluptate velit esse cillum dolore eu fugiat nulla pariatur.</p>
  <div class="btn" style="left:632px;top:1306px;width:150px">Learn More <span class="gold">›</span></div>
</section>

<section class="services">
  <h2 class="section-title" style="left:0;width:1200px;text-align:center;top:1598px">Our <span class="gold">Services</span></h2>
  <div class="rule" style="left:558px;top:1666px;width:84px"></div>

  <article class="service-card" style="left:143px">
    <div class="service-icon"><svg width="44" height="44" viewBox="0 0 44 44" fill="none" stroke="#fff" stroke-width="2"><rect x="9" y="5" width="24" height="32" rx="2"/><line x1="14" y1="13" x2="28" y2="13"/><line x1="14" y1="19" x2="28" y2="19"/><line x1="14" y1="25" x2="23" y2="25"/></svg></div>
    <h3>General<br>Contracting</h3>
    <p>Lorem ipsum dolor sit amet, consectetur adipi mod tempor incididunt abore et dolore</p>
  </article>
  <article class="service-card" style="left:377px">
    <div class="service-icon"><svg width="44" height="44" viewBox="0 0 44 44" fill="none" stroke="#fff" stroke-width="2"><rect x="6" y="10" width="28" height="28" rx="2"/><path d="M16 30l2-7 16-16 5 5-16 16z"/></svg></div>
    <h3>Design-build<br>Construction</h3>
    <p>Lorem ipsum dolor sit amet, consectetur adipi mod tempor incididunt abore et dolore</p>
  </article>
  <article class="service-card" style="left:611px">
    <div class="service-icon"><svg width="44" height="44" viewBox="0 0 44 44" fill="none" stroke="#fff" stroke-width="2"><ellipse cx="17" cy="16" rx="10" ry="4"/><path d="M7 16v16c0 2 4.5 4 10 4s10-2 10-4V16"/><path d="M7 24c0 2 4.5 4 10 4s10-2 10-4"/><circle cx="31" cy="13" r="6"/></svg></div>
    <h3>Disaster<br>Recovery</h3>
    <p>Lorem ipsum dolor sit amet, consectetur adipi mod tempor incididunt abore et dolore</p>
  </article>
  <article class="service-card" style="left:845px">
    <div class="service-icon"><svg width="44" height="44" viewBox="0 0 44 44" fill="none" stroke="#fff" stroke-width="2"><path d="M22 20v-8"/><path d="M22 12c-6 0-8-4-8-7 5 0 8 2 8 7z"/><path d="M22 12c6 0 8-4 8-7-5 0-8 2-8 7z"/><path d="M6 28h8l6 3h8c2 0 2 3 0 3h-8"/><path d="M28 33l8-5c2-1 3 1 2 2l-10 8H14l-8-3"/></svg></div>
    <h3>Environmental<br>Remediation</h3>
    <p>Lorem ipsum dolor sit amet, consectetur adipi mod tempor incididunt abore et dolore</p>
  </article>
</section>

<section class="clients">
  <h2 class="section-title" style="left:0;width:1200px;text-align:center;top:2160px">Trusted Clients</h2>
  <div class="rule" style="left:558px;top:2228px;width:84px;background:#fff"></div>
  <div class="client" style="left:143px">PMX</div>
  <div class="client" style="left:330px">TQ</div>
  <div class="client small" style="left:516px">State and Local<br>Gov't Agencies</div>
  <div class="client" style="left:701px">Hospitals</div>
  <div class="client" style="left:888px">Schools</div>
</section>

<section class="contact">
  <h2 class="section-title" style="left:0;width:1200px;text-align:center;top:2655px">Get <span class="gold">In Touch</span></h2>
  <div class="rule" style="left:558px;top:2722px;width:84px"></div>
  <div class="field" style="left:140px;top:2750px;width:297px;height:62px;line-height:58px">Name</div>
  <div class="field" style="left:452px;top:2750px;width:296px;height:62px;line-height:58px">Email</div>
  <div class="field" style="left:761px;top:2750px;width:297px;height:62px;line-height:58px">Phone</div>
  <div class="field" style="left:140px;top:2829px;width:918px;height:167px;padding-top:20px">Message</div>
  <div class="btn" style="left:526px;top:3013px;width:149px">Submit Now <span>›</span></div>
</section>

<footer class="site-footer">
  <h4 class="foot-head" style="left:143px;top:3362px">SUBSCRIBE TO<br>OUR NEWSLETTER</h4>
  <div class="abs" style="left:143px;top:3434px;width:272px;height:42px;border:1px solid #555;background:#0c0c0c;font-family:'Jost',sans-serif;font-size:13px;line-height:40px;padding-left:16px">Email address</div>
  <svg class="abs" style="left:390px;top:3446px" width="16" height="16" viewBox="0 0 16 16"><path d="M1 8 15 1 11 15 8 9z" fill="#e2aa52"/></svg>
  <div class="social" style="left:145px" aria-label="Social link"></div>
  <div class="social" style="left:177px;background:#e2aa52" aria-label="Social link"></div>
  <div class="social" style="left:210px" aria-label="Social link"></div>

  <h4 class="foot-head" style="left:503px;top:3362px">CONTACT INFO</h4>
  <svg class="abs" style="left:504px;top:3420px" width="14" height="18" viewBox="0 0 14 18"><path d="M7 17S1 10 1 6.5a6 6 0 0 1 12 0C13 10 7 17 7 17z" fill="#e2aa52"/><circle cx="7" cy="6.5" r="2.2" fill="#111"/></svg>
  <div class="foot-label" style="left:546px;top:3419px">Address</div>
  <div class="foot-small" style="left:546px;top:3445px">Lorem ipsum dolor sit amet</div>
  <svg class="abs" style="left:503px;top:3478px" width="20" height="14" viewBox="0 0 20 14"><rect width="20" height="14" rx="1" fill="#e2aa52"/><path d="M1 1l9 7 9-7" fill="none" stroke="#111" stroke-width="1.6"/></svg>
  <div class="foot-label" style="left:546px;top:3474px">Email</div>
  <div class="foot-small" style="left:546px;top:3500px">info@companyname.com</div>
  <svg class="abs" style="left:503px;top:3534px" width="17" height="17" viewBox="0 0 17 17"><path d="M4 1l3 4-2 2c1 2 3 4 5 5l2-2 4 3-2 3C8 16 1 9 1 3z" fill="#e2aa52"/></svg>
  <div class="foot-label" style="left:546px;top:3530px">Phone</div>
  <div class="foot-small" style="left:546px;top:3556px">+1 888 888 8888</div>

  <h4 class="foot-head" style="left:766px;top:3362px">QUICK LINKS</h4>
  <div class="foot-link" style="left:766px;top:3418px">Home</div>
  <div class="foot-link" style="left:766px;top:3450px">About</div>
  <div class="foot-link" style="left:766px;top:3482px">Services</div>
  <div class="foot-link" style="left:766px;top:3514px">Contact</div>
  <div class="foot-link" style="left:900px;top:3418px">Terms and Condition</div>
  <div class="foot-link" style="left:900px;top:3450px">Privacy policy</div>
  <div class="foot-link" style="left:900px;top:3482px">Help</div>
  <div class="foot-link" style="left:900px;top:3514px">Support</div>

  <p class="abs" style="left:0;width:1200px;text-align:center;top:3643px;font-family:'Jost',sans-serif;font-size:15px">© Copyrights 2025 | All Rights Reserved</p>
</footer>

</body>
</html>
```